Business Card Re-Design/Update

We'd like to update out business cards. I've included our current "Style guide" which has the colour scheme of the organisation in it. I've also included the branding files with logos etc in them.

I've also included a copy of one of our existing cards so that you can see how ugly/dated they look. I'd like a fresh modern corporate look.

Target Market(s)

These are for our clients, potential clients, industry contacts - like all business cards

Contact Information for Business Card

Name
Position
Company Address - Level 1, 47 Fernby Street, Carlow Qld 4072
Direct Phone
mobile
Email
Website -www.korvalit.com.au
Logo

Colors

Designer to choose colors to be used in the design.

Requirements
Must have
• Main Logo
• Cards will need to be editable to be able to personalize them for each new employee.
Nice to have
• The MapOut, ShipWell, KeepSteady would be okay to have if they can be sensibly and professionally added to the look without detracting from the main imagery.
• Maybe they could go on the back of the card? will leave this to your creative discretion as to whether/where they fit.
Should not have
• Should not have decorative or script fonts

```html
<!DOCTYPE html>
<html lang="en">
<head>
<meta charset="utf-8">
<title>korvalIT business card</title>
<link rel="stylesheet" href="https://fonts.googleapis.com/css2?family=Questrial&family=Arimo:wght@400&family=Quicksand:wght@300&display=swap">
<style>
  :root {
    --backdrop: #8d8d8d;
    --card-white: #f3f3f3;
    --brand-red: #d71920;
    --charcoal: #3a3a3c;
    --ink: #222222;
    --rule: #444444;
    --white: #ffffff;
  }
  * { margin: 0; padding: 0; box-sizing: border-box; }
  html, body { width: 1200px; height: 1200px; overflow: hidden; }
  body { background: var(--backdrop); position: relative; font-family: "Arimo", Arial, sans-serif; }

  .card {
    position: absolute;
    top: 310px;
    height: 594px;
    box-shadow: 2px 3px 5px rgba(0,0,0,0.35);
  }

  /* Front */
  .card-front {
    left: 234px; width: 364px;
    background: var(--card-white);
    text-align: center;
    color: var(--ink);
  }
  .wordmark {
    position: absolute; top: 165px; left: 0; width: 100%;
    display: flex; align-items: center; justify-content: center; gap: 12px;
  }
  .wordmark-square { width: 26px; height: 26px; background: var(--brand-red); }
  .wordmark-name {
    font-family: "Questrial", Arial, sans-serif;
    font-size: 50px; line-height: 1; color: var(--charcoal); letter-spacing: -0.5px;
  }
  .person { position: absolute; top: 304px; left: 0; width: 100%; }
  .person-name {
    font-family: "Questrial", Arial, sans-serif;
    font-size: 22px; color: var(--brand-red); font-weight: 400; letter-spacing: 0.3px;
  }
  .person-role { font-size: 16px; margin-top: 3px; }
  .icon-rule {
    position: absolute; top: 369px; left: 60px; width: 245px; height: 22px;
    display: flex; align-items: center; gap: 3px;
  }
  .icon-rule .line { flex: 1; height: 1px; background: var(--rule); }
  .icon-rule svg { width: 20px; height: 20px; display: block; }
  .contact-list { position: absolute; top: 396px; left: 0; width: 100%; list-style: none; font-size: 16px; line-height: 21.3px; }
  .divider { position: absolute; top: 511px; left: 60px; width: 245px; height: 1px; background: #777; }
  .address { position: absolute; top: 520px; left: 0; width: 100%; font-size: 16px; line-height: 21px; font-style: normal; }

  /* Back */
  .card-back {
    left: 627px; width: 369px;
    background: linear-gradient(to bottom, var(--brand-red) 0 295px, var(--charcoal) 295px 100%);
    color: var(--white);
  }
  .back-mark {
    position: absolute; top: 250px; left: 0; width: 100%;
    display: flex; align-items: center; justify-content: center; gap: 14px;
  }
  .back-mark-square { width: 34px; height: 34px; background: var(--white); }
  .back-mark-name { font-family: "Questrial", Arial, sans-serif; font-size: 54px; line-height: 1; color: var(--white); }
  .back-web {
    position: absolute; top: 530px; left: 0; width: 100%; text-align: center;
    font-family: "Quicksand", Arial, sans-serif; font-weight: 300; font-size: 22px; letter-spacing: 0.3px;
  }
</style>
</head>
<body>
  <section class="card card-front">
    <div class="wordmark">
      <span class="wordmark-square"></span>
      <span class="wordmark-name">korvalIT</span>
    </div>

    <div class="person">
      <h1 class="person-name">MAREN TOLLIS</h1>
      <p class="person-role">Business Development Manager</p>
    </div>

    <div class="icon-rule">
      <span class="line"></span>
      <svg viewBox="0 0 20 20" aria-label="phone"><rect width="20" height="20" rx="2" fill="#d71920"/><path d="M6 4l2.5 0 1 3-1.5 1.2a8 8 0 0 0 3.8 3.8L13 10.5l3 1V14a2 2 0 0 1-2 2A10 10 0 0 1 4 6a2 2 0 0 1 2-2z" fill="#fff"/></svg>
      <svg viewBox="0 0 20 20" aria-label="mobile"><rect width="20" height="20" rx="2" fill="#d71920"/><rect x="6.5" y="3.5" width="7" height="13" rx="1.2" fill="none" stroke="#fff" stroke-width="1.6"/><circle cx="10" cy="14.3" r="0.9" fill="#fff"/></svg>
      <svg viewBox="0 0 20 20" aria-label="fax"><rect width="20" height="20" rx="2" fill="#d71920"/><rect x="6" y="3.5" width="8" height="4" fill="#fff"/><rect x="3.5" y="8" width="13" height="6" rx="1" fill="#fff"/><rect x="6" y="12" width="8" height="4.5" fill="#fff" stroke="#d71920" stroke-width="1"/></svg>
      <svg viewBox="0 0 20 20" aria-label="email"><rect width="20" height="20" rx="2" fill="#d71920"/><rect x="3.5" y="5.5" width="13" height="9" fill="#fff"/><path d="M3.5 5.5l6.5 5 6.5-5" fill="none" stroke="#d71920" stroke-width="1.2"/></svg>
      <svg viewBox="0 0 20 20" aria-label="website"><rect width="20" height="20" rx="2" fill="#d71920"/><circle cx="10" cy="10" r="6.5" fill="#fff"/><ellipse cx="10" cy="10" rx="2.8" ry="6.5" fill="none" stroke="#d71920" stroke-width="1"/><path d="M3.5 10h13" stroke="#d71920" stroke-width="1"/></svg>
      <span class="line"></span>
    </div>

    <ul class="contact-list">
      <li>+61 (0)412 555 068</li>
      <li>+61 (0)7 3555 0142</li>
      <li>+61 (0)7 3555 0198</li>
      <li>mtollis@korvalit.com.au</li>
      <li>www.korvalit.com.au</li>
    </ul>

    <div class="divider"></div>

    <address class="address">Level 1, 47 Fernby Street<br>Carlow Qld 4072</address>
  </section>

  <section class="card card-back">
    <div class="back-mark">
      <span class="back-mark-square"></span>
      <span class="back-mark-name">korvalIT</span>
    </div>
    <p class="back-web">www.korvalit.com.au</p>
  </section>
</body>
</html>
```